buisnes card for Gentle Tide Reflexology

I need a new business card with my information
Hedwig Brommelsiek
MPLVA,KTZQ,RN(Grermany)
Cranio-Sacral Reflexology
Facial Reflexology, Veldmarkmethod TM
Nerve point Reflexology
41576 Marrowfield Road
Abbotsford,BC
Gentletidereflexology.ca
I would like the design to show that I work mostly with clients that have health problems.(80% are back/spine related problems).
I would like the card to be professional as well as inviting. I like nature aspects as well.
I have two websites that I like so you have an Idea what kind of design speaks to me.
1. www.pondorava.ca the art of healing (Chilliwack)
2.www.quietharbourdoula.ca (Abbotsford)

My treatment room is blue and the outside of our house is dark blue and grey. That are colors that could be incorporated

Target Market(s)

clients that are looking for a more natural approach to their health issues

Industry/Entity Type

Health And Wellness

Contact Information for Business Card

Hedwig Brommelsiek
MPLVA,KTZQ,RN(Grermany)
Cranio-Sacral Reflexology
Nerve point Reflexology
41576 Marrowfield Road
Abbotsford,BC
Gentletidereflexology.ca

Colors
0355a3
0492cd

Requirements
Must have
• name, address, phonenumber
Nice to have
• 1. www.pondorava.ca the art of healing (Chilliwack)
• 2.www.quietharbourdoula.ca (Abbotsford)
• This are designs that I like.

```html
<!DOCTYPE html>
<html lang="en">
<head>
<meta charset="utf-8">
<title>Gentle Tide Reflexology – Business Card</title>
<link href="https://fonts.googleapis.com/css2?family=Arimo:wght@400;700&display=swap" rel="stylesheet">
<style>
  :root {
    --page-bg: #1c1c1c;
    --card-blue: #0355a3;
    --card-blue-light: #0492cd;
    --card-blue-deep: #0a4f9e;
    --glow-blue: #4a86d0;
    --figure-blue: #7fb4ee;
    --spine-orange: #f0a030;
    --text-white: #ffffff;
  }
  html, body {
    margin: 0;
    padding: 0;
    width: 1200px;
    height: 902px;
    overflow: hidden;
    background: var(--page-bg);
    font-family: "Arimo", Arial, sans-serif;
  }
  .business-card {
    position: absolute;
    left: 100px;
    top: 166px;
    width: 1000px;
    height: 570px;
    border-radius: 32px;
    overflow: hidden;
    background: linear-gradient(100deg, var(--card-blue) 0%, var(--card-blue-deep) 45%, #2d66b8 75%, var(--card-blue) 100%);
    color: var(--text-white);
  }
  .anatomy-visual {
    position: absolute;
    left: 520px;
    top: 0;
    width: 480px;
    height: 570px;
    background:
      radial-gradient(ellipse 30% 42% at 58% 48%, rgba(240,160,48,0.55) 0%, rgba(240,160,48,0) 70%),
      radial-gradient(ellipse 48% 60% at 55% 48%, var(--figure-blue) 0%, var(--glow-blue) 45%, rgba(74,134,208,0) 100%);
  }
  .holder-name {
    position: absolute;
    left: 64px;
    top: 74px;
    margin: 0;
    font-size: 40px;
    font-weight: 700;
    line-height: 1;
    letter-spacing: 0.2px;
  }
  .credentials {
    position: absolute;
    left: 66px;
    top: 120px;
    margin: 0;
    font-size: 23px;
    line-height: 1;
  }
  .services {
    position: absolute;
    left: 68px;
    top: 176px;
    margin: 0;
    padding: 0;
    list-style: none;
    font-size: 24px;
    line-height: 33px;
  }
  .contact-list {
    position: absolute;
    left: 68px;
    top: 292px;
    margin: 0;
    padding: 0;
    list-style: none;
    font-size: 24px;
  }
  .contact-item {
    display: flex;
    align-items: center;
    height: 38px;
  }
  .contact-icon {
    width: 24px;
    height: 24px;
    margin-right: 20px;
    flex: none;
  }
  .address {
    position: absolute;
    left: 68px;
    top: 434px;
    margin: 0;
    font-style: normal;
    font-size: 28px;
    line-height: 38px;
  }
</style>
</head>
<body>
  <section class="business-card">
    <div class="anatomy-visual" role="img" aria-label="Translucent blue anatomical figure bending forward and holding the lower back, with the spine highlighted in glowing orange"></div>

    <h1 class="holder-name">Hedwig Brommelsiek</h1>
    <p class="credentials">MPLVA,KTZQ,RN(Grermany)</p>

    <ul class="services">
      <li>Cranio-Sacral Reflexology</li>
      <li>Facial Reflexology, Veldmarkmethod TM</li>
      <li>Nerve point Reflexology</li>
    </ul>

    <ul class="contact-list">
      <li class="contact-item">
        <svg class="contact-icon" viewBox="0 0 24 24" aria-hidden="true">
          <rect width="24" height="24" rx="2" fill="#ffffff"/>
          <path d="M8 5c1 0 1.6 2.6 1.6 3.3 0 .8-1.2 1-1 1.8.5 1.8 1.6 3.4 3 4.6.6.4 1.2-.6 1.9-.4.8.3 2.8 1.7 2.5 2.6-.4 1.2-1.6 2-2.8 1.7C9.6 17.6 6.4 13.6 5.8 9.2 5.6 7.5 6.6 5 8 5z" fill="#0355a3"/>
        </svg>
        <span>000.000.0000</span>
      </li>
      <li class="contact-item">
        <svg class="contact-icon" viewBox="0 0 24 24" aria-hidden="true">
          <rect width="24" height="24" rx="2" fill="#ffffff"/>
          <rect x="4" y="6.5" width="16" height="11" fill="none" stroke="#0355a3" stroke-width="1.6"/>
          <path d="M4 6.5l8 6.5 8-6.5M4 17.5l6-5.5M20 17.5l-6-5.5" fill="none" stroke="#0355a3" stroke-width="1.6"/>
        </svg>
        <span>your@gentletidemail.com</span>
      </li>
      <li class="contact-item">
        <svg class="contact-icon" viewBox="0 0 24 24" aria-hidden="true">
          <rect width="24" height="24" rx="2" fill="#ffffff"/>
          <circle cx="12" cy="12" r="7" fill="#0355a3"/>
          <path d="M8 9c1.5-.5 2.5.5 3 1.5s-1 2-.5 3 1.5 1 1 2.5M14 7.5c.5 1 1.8 1 2.5 2M15 14c1 0 1.5 1 1.5 2" fill="none" stroke="#ffffff" stroke-width="1.2"/>
        </svg>
        <span>Gentletidereflexology.ca</span>
      </li>
    </ul>

    <address class="address">
      41576 Marrowfield Road<br>
      Abbotsford,BC
    </address>
  </section>
</body>
</html>
```